Corvane Capital Business Cards

These are professional business cards that are for my family office.
Put fake emails and phone numbers as of now until I finalize those components. This family office controls my families investments, assets, and future. The cards should be professional.
..
.
.
.
I just uploaded another variation of a logo I would like to see as a business card to I am inbeteen which logo to use

Target Market(s)

business

Industry/Entity Type

business

Contact Information for Business Card

Professional, wealth related, finance related.

Requirements
Must have
• Logo

```html
<!DOCTYPE html>
<html lang="en">
<head>
<meta charset="UTF-8">
<title>Corvane Capital Business Cards</title>
<link rel="stylesheet" href="https://fonts.googleapis.com/css2?family=Cinzel:wght@600&family=Poppins:wght@300;400;500;600&display=swap">
<style>
  :root {
    --page: #e3e7e9;
    --card-light: #f0f0f0;
    --navy: #161c29;
    --band-end: #9c9c9e;
    --white: #ffffff;
  }
  * { margin: 0; padding: 0; box-sizing: border-box; }
  html, body { width: 1200px; height: 960px; overflow: hidden; }
  body { background: var(--page); position: relative; font-family: "Poppins", sans-serif; }

  .card { position: absolute; left: 250px; width: 701px; height: 400px; overflow: hidden; }
  .card--front { top: 70px; background: var(--card-light); }
  .card--back { top: 510px; background: var(--navy); }

  .front-wordmark {
    position: absolute; left: 0; right: 0; top: 0; bottom: 0;
    display: flex; align-items: center; justify-content: center;
    font-family: "Cinzel", serif; font-weight: 600; font-size: 38px;
    color: var(--navy); letter-spacing: 0.5px;
  }

  .back-shape { position: absolute; inset: 0; }

  .back-wordmark {
    position: absolute; right: 26px; top: 30px;
    font-family: "Cinzel", serif; font-weight: 600; font-size: 31px;
    color: var(--white); letter-spacing: 0.3px; text-align: right;
  }

  .name-band {
    position: absolute; left: 415px; right: 0; top: 168px; height: 64px;
    background: linear-gradient(90deg, var(--navy) 0%, #3a3d46 45%, var(--band-end) 100%);
  }
  .person { position: absolute; right: 24px; top: 172px; text-align: right; color: var(--white); }
  .person__name { font-size: 30px; line-height: 36px; }
  .person__first { font-weight: 600; }
  .person__last { font-weight: 300; }
  .person__title { font-size: 16px; font-weight: 500; line-height: 18px; }

  .address {
    position: absolute; right: 25px; top: 245px; text-align: right;
    color: var(--white); font-size: 16.5px; line-height: 23px; font-weight: 400;
  }

  .contacts { position: absolute; right: 18px; top: 310px; list-style: none; color: var(--white); }
  .contacts li {
    display: flex; align-items: center; justify-content: flex-end;
    font-size: 17px; line-height: 23.5px; gap: 10px;
  }
  .contacts svg { width: 15px; height: 15px; fill: none; stroke: var(--white); stroke-width: 1.6; }
</style>
</head>
<body>

  <section class="card card--front" aria-label="Card front">
    <div class="front-wordmark">Corvane Capital</div>
  </section>

  <section class="card card--back" aria-label="Card back">
    <svg class="back-shape" viewBox="0 0 701 400" aria-hidden="true">
      <rect x="0" y="0" width="209" height="400" fill="var(--card-light)"/>
      <circle cx="209" cy="200" r="209" fill="var(--card-light)"/>
    </svg>

    <div class="back-wordmark">Corvane Capital</div>

    <div class="name-band"></div>
    <div class="person">
      <div class="person__name"><span class="person__first">Marta</span> <span class="person__last">Delvik</span></div>
      <div class="person__title">Founder &amp; CEO</div>
    </div>

    <address class="address" style="font-style: normal;">
      1840 Linden Ave. Suite 300<br>
      Harlow, TX 75501
    </address>

    <ul class="contacts">
      <li>(555) 214-3370
        <svg viewBox="0 0 16 16" aria-hidden="true"><path d="M4 1.5l2 3-1.3 1.3a8 8 0 0 0 5.5 5.5L11.5 10l3 2-1.2 2.3C7.5 14.5 1.5 8.5 1.7 2.7z"/></svg>
      </li>
      <li>info@corvanecapital.com
        <svg viewBox="0 0 16 16" aria-hidden="true"><circle cx="8" cy="8" r="6.5"/><path d="M1.5 8h13M8 1.5c-3 3.5-3 9.5 0 13M8 1.5c3 3.5 3 9.5 0 13"/></svg>
      </li>
      <li>www.corvanecapital.com
        <svg viewBox="0 0 16 16" aria-hidden="true"><rect x="1.5" y="3.5" width="13" height="10" rx="1"/><path d="M1.5 4l6.5 5 6.5-5"/></svg>
      </li>
    </ul>
  </section>

</body>
</html>
```